Website for Torvel Capital - investment banking firm

We have a corporate identity (thanks to Ravinka/31842) and want to extend that into a website design.  See the attached zipped files.
We have software folks in-house to do the coding.
See the attached Project Brief & Notes for more details.  Don't worry about the actual text - lorem ipsum will be fine.
The server will be Apache.
Thank you!
Desmond

Industry/Entity Type
Investment

```html
<!DOCTYPE html>
<html lang="en">
<head>
<meta charset="utf-8">
<title>Torvel Capital</title>
<link rel="stylesheet" href="https://fonts.googleapis.com/css2?family=Raleway:wght@400;500&family=Open+Sans:wght@400;600&family=Roboto:wght@400;500&family=Merriweather:wght@300;400&display=swap">
<style>
:root{
  --blue:#1c4a93;
  --blue-deep:#163d7d;
  --blue-bg:#1d4a8f;
  --ink:#222;
  --grey:#555;
  --line:#dcdcdc;
  --red:#e0141b;
  --accent:#e2582a;
  --white:#fff;
}
*{box-sizing:border-box;margin:0;padding:0}
html,body{width:1200px;height:968px;overflow:hidden}
body{position:relative;background:linear-gradient(180deg,#1f4e96 0%,#1a4486 100%);font-family:"Open Sans",sans-serif;color:var(--ink)}
a{text-decoration:none;color:inherit}
.backdrop{position:absolute;left:0;top:0;width:1200px;height:600px}
.brand{position:absolute;left:147px;top:38px;display:flex;align-items:center;gap:12px}
.brand-square{width:40px;height:40px;background:var(--blue)}
.brand-name{font-family:"Merriweather",serif;font-size:33px;font-weight:400;color:var(--blue);letter-spacing:.5px}
.util-contact{position:absolute;left:762px;top:37px;font-size:12.5px;color:#777;font-weight:600}
.util-contact::before,.banking::before{content:"›";margin-right:8px;font-size:16px}
.banking{position:absolute;left:895px;top:30px;width:157px;height:32px;background:#000;color:#fff;font-size:12.5px;font-weight:600;display:flex;align-items:center;padding-left:12px}
.nav{position:absolute;left:148px;top:135px;width:905px;height:41px;background:var(--blue);display:flex;align-items:center;padding-left:16px;z-index:3}
.nav-home{width:20px;height:18px;margin-right:12px}
.nav a{color:#fff;font-size:15px;padding:0 14px;border-left:1px solid rgba(255,255,255,.18);line-height:18px}
.search{position:absolute;right:16px;top:10px;width:224px;height:22px;background:#fff;border-radius:2px}
.search-btn{position:absolute;right:2px;top:2px;width:22px;height:18px;background:#a7a7b5;border-radius:2px}
.hero{position:absolute;left:148px;top:176px;width:905px;height:416px;overflow:hidden}
.hero-photo{position:absolute;inset:0;background:radial-gradient(ellipse at 78% 40%,#d8a83a 0%,#a8781c 22%,#3b4e8a 55%,#1b2550 100%)}
.hero-photo::after{content:"";position:absolute;left:0;right:0;bottom:0;height:150px;background:linear-gradient(180deg,rgba(0,0,0,0),#b58a2a 60%,#6e4f14)}
.curve{position:absolute;left:0;top:0;z-index:2}
.hero-copy{position:absolute;left:164px;top:226px;z-index:4;width:420px}
.hero-title{font-family:"Raleway",sans-serif;font-weight:400;font-size:38px;line-height:42px;color:#555}
.hero-title span{color:var(--blue)}
.hero-text{margin-top:18px;font-size:17.5px;line-height:22px;color:#111}
.hero-btn{display:inline-flex;align-items:center;justify-content:center;margin-top:16px;width:148px;height:36px;background:var(--blue);color:#fff;font-family:"Roboto",sans-serif;font-size:14.5px;border:1px solid #123b7a}
.tabs{position:absolute;left:521px;top:554px;width:532px;height:38px;background:linear-gradient(180deg,#f1f1f1,#dadada);display:flex;z-index:4}
.tab{flex:1;display:flex;align-items:center;justify-content:space-between;padding:0 14px 0 20px;font-size:12.5px;font-weight:600;color:#222}
.tab svg{width:12px;height:8px}
.panel{position:absolute;left:148px;top:592px;width:905px;height:198px;background:#fff}
.map{position:absolute;left:26px;top:38px;width:294px;height:130px;background:linear-gradient(135deg,#e6e4df,#cfd8de);border:4px solid #fafafa;box-shadow:0 1px 4px rgba(0,0,0,.3)}
.col{position:absolute;top:36px}
.col h3{font-family:"Merriweather",serif;font-weight:300;font-size:16px;color:#333;margin-bottom:8px}
.news{left:366px;width:170px;font-family:"Roboto",sans-serif;font-size:11px;line-height:15.5px;color:#333}
.news .alert{color:var(--red);font-weight:500;margin-top:3px}
.divider{position:absolute;top:20px;width:1px;height:166px;background:var(--line)}
.quick{left:577px;width:140px}
.quick ul{list-style:none}
.quick li{font-family:"Roboto",sans-serif;font-size:10.5px;font-weight:500;color:#222;padding:3px 0 4px 15px;border-bottom:1px solid #e6e6e6;position:relative;margin-left:-8px;padding-left:23px}
.quick li::before,.video-btn::before{content:"›";position:absolute;left:10px;top:0;color:var(--accent);font-size:14px}
.more{margin-top:8px;margin-left:-8px;width:142px;height:26px;border:1px solid #ccc;background:linear-gradient(#fff,#f0f0f0);font-family:"Roboto",sans-serif;font-size:12px;display:flex;align-items:center;padding:0 8px;justify-content:space-between}
.more b{color:var(--accent);font-weight:500;margin-right:6px}
.video{left:742px;width:160px}
.video p{font-family:"Roboto",sans-serif;font-size:11px;line-height:16px;color:#333;width:92px;position:relative;z-index:2}
.agent{position:absolute;left:812px;top:54px;width:93px;height:132px;background:linear-gradient(160deg,#d9c7a5,#f2ede4 60%,#e2e2e2);border-radius:40px 0 0 0}
.video-btn{position:absolute;left:742px;top:148px;width:156px;height:26px;border:1px solid #ccc;background:linear-gradient(#fff,#f0f0f0);font-family:"Roboto",sans-serif;font-size:12px;display:flex;align-items:center;padding-left:22px;z-index:2}
.video-btn::before{top:3px}
.foot{position:absolute;top:810px;left:148px;width:905px}
.foot-col{position:absolute;top:0;list-style:none}
.foot-col li{height:27.5px;font-family:"Roboto",sans-serif;font-size:12.5px;color:#e8eef8;position:relative;padding-left:16px}
.foot-col li::before{content:"›";position:absolute;left:0;top:-3px;font-size:17px}
.foot-icons li{padding-left:42px}
.foot-icons li::before{content:"";left:0;top:-6px;width:24px;height:24px;background:#fff;border-radius:2px}
.rule{position:absolute;left:148px;top:907px;width:905px;height:1px;background:rgba(255,255,255,.2)}
.copyright{position:absolute;left:147px;top:926px;font-family:"Roboto",sans-serif;font-size:12.5px;color:#e8eef8}
</style>
</head>
<body>
<svg class="backdrop" width="1200" height="600" viewBox="0 0 1200 600" aria-hidden="true">
  <path d="M0 0H881C860 70 838 110 812 150L783 176H0Z" fill="#fff"/>
  <path d="M0 176H148V458C95 448 45 433 0 415Z" fill="#fff"/>
</svg>

<div class="brand"><span class="brand-square"></span><span class="brand-name">Torvel Capital</span></div>
<a class="util-contact" href="#">Contact Us</a>
<a class="banking" href="#">Online Banking</a>

<nav class="nav">
  <svg class="nav-home" viewBox="0 0 20 18" aria-label="Home"><path d="M10 1L1 9h3v8h4.5v-5h3v5H16V9h3z" fill="#fff"/></svg>
  <a href="#">About</a><a href="#">Services</a><a href="#">Current Engagements</a><a href="#">Completed Transactions</a>
  <div class="search"><span class="search-btn"></span></div>
</nav>

<section class="hero">
  <div class="hero-photo" role="img" aria-label="Stacks of gold coins in front of a glowing stock market chart"></div>
  <svg class="curve" width="905" height="416" viewBox="0 0 905 416" aria-hidden="true">
    <path d="M0 0H635C560 150 380 300 190 300C120 300 50 290 0 282Z" fill="#fff"/>
  </svg>
</section>
<div class="hero-copy">
  <h1 class="hero-title"><span>Trusted or</span> Disciplined Effective?</h1>
  <p class="hero-text">Torvel Capital is an independent investment bank working for buyers in a number of industries. We</p>
  <a class="hero-btn" href="#">Read More</a>
</div>
<div class="tabs">
  <div class="tab">Financial Money<svg viewBox="0 0 12 8"><path d="M1 7l5-5 5 5" stroke="#999" stroke-width="1.5" fill="none"/></svg></div>
  <div class="tab">Capital Invesment<svg viewBox="0 0 12 8"><path d="M1 7l5-5 5 5" stroke="#999" stroke-width="1.5" fill="none"/></svg></div>
  <div class="tab">Financia statment<svg viewBox="0 0 12 8"><path d="M1 7l5-5 5 5" stroke="#999" stroke-width="1.5" fill="none"/></svg></div>
</div>

<section class="panel">
  <div class="map" role="img" aria-label="Street map with branch location pins"></div>
  <div class="col news">
    <h3>What's new?</h3>
    <p>Bank Super is</p>
    <p>here</p>
    <p class="alert">VIP Enhanced Online Security</p>
    <p class="alert">Fraud Alert: Hoax Email and Phone Calls</p>
    <p>Get $300 for referring a</p>
  </div>
  <span class="divider" style="left:553px"></span>
  <div class="col quick">
    <h3>Quick links</h3>
    <ul><li>About</li><li>Services</li><li>Current Engagements</li><li>Completed Transactions</li></ul>
    <div class="more"><span><b>+</b>More</span><svg width="10" height="6" viewBox="0 0 10 6"><path d="M0 6L5 0L10 6Z" fill="#aaa"/></svg></div>
  </div>
  <span class="divider" style="left:729px"></span>
  <div class="agent" role="img" aria-label="Call centre agent wearing a headset"></div>
  <div class="col video">
    <h3>Video Call Centre</h3>
    <p>Talk to us Services face-to-face via PC or laptop</p>
  </div>
  <a class="video-btn" href="#">Make a Video Call</a>
</section>

<footer>
  <div class="foot">
    <ul class="foot-col" style="left:1px"><li>VIP Enhanced Online Security</li><li>Sitemap</li><li>Lost or stolen cards</li></ul>
    <ul class="foot-col" style="left:204px"><li>Disclosure documents</li><li>Dispute resolution</li><li>Find a branch</li></ul>
    <ul class="foot-col" style="left:391px"><li>VIP Enhanced Online Security</li><li>Sitemap</li><li>Lost or stolen cards</li></ul>
    <ul class="foot-col foot-icons" style="left:613px"><li>VIP Enhanced Online Security</li><li>Sitemap</li><li>Lost or stolen cards</li></ul>
  </div>
  <div class="rule"></div>
  <p class="copyright">Copyright Torvel ABN 12 480 316 972 AFSL/japan Credit Licence 508163</p>
</footer>
</body>
</html>
```